Concert Venue Show Posters (ongoing job too)

Looking for a designer for ongoing project to create posters for each of our concerts coming to the venue. We have a budget of $35-45.00 per poster and on average do 5-12 per month. We’re looking for simple, unique design template going forward as part of our branding.

We hope to establish a long term relationship with someone to do this work on an ongoing adhoc basis.

Goal is to simple tell folks who, where, and when.

Creative needs to delivered in Photoshop PSD file format in two sizes; 24" x 36" used onsite in lobby and 11" x 17" for offsite marketing distribution.

We’ll supply all approved artwork and information for you to use although sometimes what we get from management sucks.

You can look at some of our older posters here
http://brookhallstage.example-photos.com/Other/Posters/

Our website (it’s in re-design now)
http://www.brookhallstage.example

Our new website format moving toward this as template
http://www.quillhousehall.example/event/418806-merle-lanterns-portland/

Thoughts? Ideas? Included artwork to see some samples.

Include these items on poster
Brook HALL logo
Artists Name
Gideon Vale and the Drifters (image with single guitar players)
Rusty Kettle (group image)
September 25, 2014
Doors 7:00
Show 8:00
You can sort of get an idea from our old posters.

PS this could lead to extra work doing our newspaper creatives too.

Project Deadline Extended
Reason: Due to weekend and workload of staff we'll make our final selection on Wednesday, August 28th by 6 PM EST. Thanks to everyone for submitting some great examples of work.

Target Market(s)

Onsite concert goers for future shows, and offsite spreading the word about shows.

Industry/Entity Type

Marketing

Requirements
Must have
• Simple is best. Not looking for bar band type posters, remember we're just letting fans know about who and when.
Nice to have
• Template, easy to reproduce show after show to keep costs down.
Should not have
• Less is more since we're just telling patons who, when, and where.

```html
<!DOCTYPE html>
<html lang="en">
<head>
<meta charset="utf-8">
<title>Gideon Vale and the Drifters — Show Poster</title>
<link rel="stylesheet" href="https://fonts.googleapis.com/css2?family=Arvo:wght@400&display=swap">
<style>
:root{
  --ink:#ffffff;
  --night:#000000;
  --deep:#0b2430;
  --teal:#1f6a78;
  --amber:#e0a043;
  --rust:#c4622e;
  --lime:#cfd64a;
  --violet:#7a4cc0;
  --cyan:#4fc3d8;
  --magenta:#d25aa8;
}
*{margin:0;padding:0;box-sizing:border-box}
html,body{width:776px;height:1200px;overflow:hidden;background:var(--night)}
.poster{position:relative;width:776px;height:1200px;overflow:hidden;background:var(--night);color:var(--ink);font-family:"Arvo",serif;font-weight:400}
.stage-photo{position:absolute;left:0;top:0;width:776px;height:960px;
  background:
    radial-gradient(circle 22px at 243px 205px, rgba(255,235,245,.95), rgba(255,200,230,.35) 60%, transparent 100%),
    radial-gradient(circle 22px at 527px 228px, rgba(255,235,245,.95), rgba(255,200,230,.35) 60%, transparent 100%),
    radial-gradient(circle 22px at 668px 236px, rgba(255,235,245,.95), rgba(255,180,230,.35) 60%, transparent 100%),
    radial-gradient(circle 20px at 42px 172px, rgba(255,220,240,.7), transparent 100%),
    radial-gradient(ellipse 200px 170px at 400px 290px, rgba(196,98,46,.9), transparent 75%),
    radial-gradient(ellipse 230px 200px at 250px 470px, rgba(224,140,60,.85), transparent 75%),
    radial-gradient(ellipse 260px 230px at 600px 480px, rgba(207,214,74,.85), transparent 75%),
    radial-gradient(ellipse 300px 160px at 160px 230px, rgba(224,200,110,.7), transparent 75%),
    radial-gradient(ellipse 220px 160px at 420px 640px, rgba(224,190,80,.55), transparent 75%),
    radial-gradient(ellipse 220px 120px at 120px 740px, rgba(79,195,216,.6), transparent 75%),
    radial-gradient(ellipse 260px 120px at 400px 760px, rgba(122,76,192,.8), transparent 75%),
    radial-gradient(ellipse 200px 130px at 700px 720px, rgba(79,195,216,.7), transparent 75%),
    radial-gradient(ellipse 160px 140px at 720px 240px, rgba(210,90,168,.45), transparent 75%),
    linear-gradient(180deg, var(--deep) 0%, #183e4a 14%, var(--teal) 40%, #3b4f7a 66%, #1a2440 78%, var(--night) 100%);}
.stage-photo::after{content:"";position:absolute;left:0;right:0;bottom:0;height:180px;background:linear-gradient(180deg,rgba(0,0,0,0) 0%,rgba(0,0,0,.85) 45%,var(--night) 100%)}
.header{position:absolute;top:34px;left:0;width:100%;text-align:center}
.date-row{display:flex;align-items:center;justify-content:center;gap:14px}
.rule{flex:1;height:12px;border-top:3px solid var(--ink);border-bottom:3px solid var(--ink)}
.date{font-size:40px;letter-spacing:1px;line-height:1;white-space:nowrap}
.times{font-size:27px;letter-spacing:1px;margin-top:14px;line-height:1}
.presenters{position:absolute;top:888px;left:0;width:100%;display:flex;justify-content:center;align-items:center;gap:22px}
.partner{display:flex;align-items:center;gap:8px;font-size:20px;line-height:1.1}
.partner .dot{width:58px;height:58px;border-radius:50%;background:var(--ink)}
.venue{font-size:34px;line-height:1;text-align:center}
.presents{position:absolute;top:980px;width:100%;text-align:center;font-size:21px;line-height:1}
.headliner{position:absolute;top:1018px;width:100%;text-align:center;font-size:84px;line-height:1;font-weight:400}
.support{position:absolute;top:1118px;width:100%;text-align:center;font-size:36px;line-height:1}
</style>
</head>
<body>
<main class="poster">
  <div class="stage-photo" role="img" aria-label="Concert photo: long-haired guitarist playing on a lit stage above a cheering crowd with raised hands"></div>
  <header class="header">
    <div class="date-row">
      <span class="rule"></span>
      <span class="date">SEPTEMBER 25, 2014</span>
      <span class="rule"></span>
    </div>
    <p class="times">DOORS 7:00 | SHOW 8:00</p>
  </header>
  <div class="presenters">
    <span class="partner"><span class="dot"></span>Rusty<br>Kettle</span>
    <span class="venue">Brook<br>HALL</span>
  </div>
  <p class="presents">Presents</p>
  <h1 class="headliner">Gideon Vale</h1>
  <p class="support">and the Drifters</p>
</main>
</body>
</html>
```